Banner Design 4040mm W x 2190mm H

Design a glamorous and exciting 4040mm W x 2190mm H backdrop for the QLMRT Velvet Harbour Gala at the luxurious Tamsin Hall, Vellora, Whitcombe Quay, Sydney. This exciting backdrop should be spectacular so that people will be excited to take photos in front of it.
Design Colours preferred is black and pink.
Please include our website on the banner www.qlmrt.org.au
Should include the words "QLMRT Velvet Harbour Gala" as the main attraction on the banner.
Please include "Thank you to our sponsors" and include the logo of the sponsors.
Sponsors:
Brenwick Pathology
NorthGlen Radiology
KTV Diagnostic Imaging
Harbin Legal Partners
Denhams
Banner Template:
4040mm W x 2190mm H Single Sided (.AI)
https://files.examplestore.net/d/8Rk2mZpQ7vLx3TnW5yBc/view
QLMRT Logo:
Can be obtained from our website www.qlmrt.org.au

```html
<!DOCTYPE html>
<html lang="en">
<head>
<meta charset="utf-8">
<title>QLMRT Velvet Harbour Gala – Backdrop</title>
<link rel="stylesheet" href="https://fonts.googleapis.com/css2?family=Poppins:wght@400;500;600;700&family=Yellowtail&display=swap">
<style>
  :root {
    --page-bg: #e4e4e4;
    --paper: #ffffff;
    --magenta-deep: #6e0a4f;
    --magenta: #b0147f;
    --magenta-bright: #e23aa8;
    --pill: #c0138d;
    --ink: #1a1a1a;
    --gold-dark: #9c7428;
    --gold-light: #f8f07c;
    --gold-mid: #d2ae4a;
    --sponsor-red: #e0245e;
    --sponsor-navy: #1c2f8a;
    --sponsor-purple: #7a55c9;
    --sponsor-gold: #c9a232;
    --sponsor-blue: #0d4f9c;
  }
  * { box-sizing: border-box; margin: 0; padding: 0; }
  html, body {
    width: 910px; height: 1200px; overflow: hidden;
    background: var(--page-bg);
    font-family: "Poppins", sans-serif;
  }
  .backdrop {
    position: absolute; left: 49px; top: 380px;
    width: 812px; height: 439px;
    background: var(--paper);
    box-shadow: 0 6px 18px rgba(0,0,0,.25);
    overflow: hidden;
  }
  .glitter-field {
    position: absolute; left: 0; top: 0; width: 812px; height: 262px;
    background:
      radial-gradient(circle at 20% 30%, rgba(255,120,210,.35), transparent 40%),
      radial-gradient(circle at 75% 70%, rgba(255,90,200,.3), transparent 45%),
      linear-gradient(180deg, var(--magenta) 0%, var(--magenta-deep) 55%, var(--magenta) 100%);
  }
  .client-mark {
    position: absolute; left: 45px; top: 105px;
    display: flex; align-items: center; gap: 10px;
    color: var(--paper); font-weight: 600; font-size: 34px; letter-spacing: 1px;
  }
  .client-mark .dot {
    width: 26px; height: 26px; border-radius: 50%; background: var(--paper);
  }
  .headline {
    position: absolute; left: 0; top: 0; width: 812px; height: 262px;
  }
  .headline .acronym {
    font-family: "Poppins", sans-serif; font-weight: 600; fill: var(--paper);
  }
  .headline .event-name {
    font-family: "Yellowtail", cursive; fill: var(--paper);
    stroke: #3a0a2c; stroke-width: 1.2px; paint-order: stroke;
  }
  .gold-tear { position: absolute; left: 0; top: 0; width: 812px; height: 439px; }
  .thanks {
    position: absolute; left: 63px; top: 323px;
    font-weight: 600; font-size: 13.5px; line-height: 17px;
    color: var(--ink); text-transform: uppercase;
  }
  .thanks .accent { color: var(--pill); }
  .sponsors { position: absolute; left: 0; top: 0; }
  .sponsor {
    position: absolute; top: 327px; height: 22px;
    display: flex; align-items: center; gap: 5px;
    font-weight: 600; white-space: nowrap; line-height: 1.05;
  }
  .sponsor .square { width: 10px; height: 10px; flex: none; }
  .sponsor .circle { width: 12px; height: 12px; border-radius: 50%; flex: none; }
  .sponsor--brenwick { left: 203px; color: var(--sponsor-red); font-size: 11.5px; }
  .sponsor--brenwick .square { background: var(--sponsor-navy); }
  .sponsor--northglen { left: 338px; color: var(--sponsor-navy); font-size: 9.5px; }
  .sponsor--northglen .circle { background: var(--sponsor-navy); }
  .sponsor--ktv { left: 474px; color: var(--sponsor-purple); font-size: 9.5px; }
  .sponsor--ktv .circle { background: var(--sponsor-purple); }
  .sponsor--harbin { left: 597px; color: var(--sponsor-gold); font-size: 8.5px; }
  .sponsor--denhams { left: 698px; color: var(--sponsor-blue); font-size: 11px; }
  .sponsor--denhams .square { background: var(--sponsor-blue); }
  .web-pill {
    position: absolute; left: 226px; top: 371px; width: 361px; height: 33px;
    border-radius: 9px; background: var(--pill);
    display: flex; align-items: center; justify-content: center;
    color: var(--paper); font-size: 21px; letter-spacing: 6px; font-weight: 400;
  }
  .web-pill strong { font-weight: 700; }
</style>
</head>
<body>
  <main class="backdrop">
    <div class="glitter-field" role="img" aria-label="Sparkling magenta glitter bokeh background"></div>

    <div class="client-mark"><span class="dot"></span>QLMRT</div>

    <svg class="headline" viewBox="0 0 812 262" aria-label="QLMRT Velvet Harbour Gala">
      <text class="acronym" x="244" y="156" font-size="150" textLength="529" lengthAdjust="spacingAndGlyphs">QLMRT</text>
      <text class="event-name" x="236" y="222" font-size="70" textLength="540" lengthAdjust="spacingAndGlyphs">Velvet Harbour Gala</text>
    </svg>

    <svg class="gold-tear" viewBox="0 0 812 439" aria-hidden="true">
      <defs>
        <linearGradient id="gold" x1="0" x2="1" y1="0" y2="0">
          <stop offset="0" stop-color="var(--gold-dark)"/>
          <stop offset=".18" stop-color="var(--gold-light)"/>
          <stop offset=".45" stop-color="var(--gold-light)"/>
          <stop offset=".7" stop-color="var(--gold-dark)"/>
          <stop offset="1" stop-color="var(--gold-mid)"/>
        </linearGradient>
      </defs>
      <path fill="url(#gold)" d="M0,255 L60,252 L120,248 L150,244 L200,246 L260,243 L330,246 L400,247 L470,243 L540,246 L600,241 L660,240 L720,238 L780,236 L812,237 L812,300 L800,290 L785,296 L770,287 L745,292 L730,283 L700,289 L690,281 L660,285 L640,280 L610,286 L590,283 L560,291 L540,288 L520,283 L495,287 L470,280 L445,289 L420,284 L395,291 L372,284 L350,290 L330,282 L300,286 L280,282 L262,293 L240,288 L215,300 L200,296 L185,305 L165,302 L150,310 L135,300 L110,291 L85,294 L60,286 L35,287 L15,282 L0,284 Z"/>
      <polyline fill="none" stroke="var(--ink)" stroke-width="2.5" stroke-linejoin="round" points="812,300 800,290 785,296 770,287 745,292 730,283 700,289 690,281 660,285 640,280 610,286 590,283 560,291 540,288 520,283 495,287 470,280 445,289 420,284 395,291 372,284 350,290 330,282 300,286 280,282 262,293 240,288 215,300 200,296 185,305 165,302 150,310 135,300 110,291 85,294 60,286 35,287 15,282 0,284"/>
    </svg>

    <p class="thanks">Thank you to<br><span class="accent">our sponsors</span></p>

    <div class="sponsors">
      <div class="sponsor sponsor--brenwick"><span class="square"></span>Brenwick Pathology</div>
      <div class="sponsor sponsor--northglen"><span class="circle"></span>NorthGlen Radiology</div>
      <div class="sponsor sponsor--ktv"><span class="circle"></span>KTV Diagnostic<br>Imaging</div>
      <div class="sponsor sponsor--harbin">Harbin Legal<br>Partners</div>
      <div class="sponsor sponsor--denhams"><span class="square"></span>Denhams</div>
    </div>

    <div class="web-pill">www.<strong>qlmrt</strong>.org.au</div>
  </main>
</body>
</html>
```